business card - Helicopter Flight Services, Flight School, etc.

We need a business card design for a new helicopter service.

We offer Helicopter Flight Services, Aerial Filming & Photography, Flight School, and Helicopter Tours. In that order.

Summit BladeAir, Inc.
Dennis Tollerby
SummitBladeair@Kestmail.com
626-418-7352

Based at the Brenwick Airport in Van Nuys, CA. The final design should communicate integrity and safety. Pictures or logos at your discretion.

Card back side - surprise me.

```html
<!DOCTYPE html>
<html lang="en">
<head>
<meta charset="utf-8">
<title>Summit BladeAir, Inc. — Business Card</title>
<link rel="stylesheet" href="https://fonts.googleapis.com/css2?family=Open+Sans:wght@400;600;700&display=swap">
<style>
  :root {
    --backdrop: #3a302c;
    --card-dark: #141414;
    --card-mid: #232323;
    --accent-blue: #1e8cf0;
    --text-light: #f2f2f2;
    --tab-line: #e8e8e8;
  }
  * { box-sizing: border-box; margin: 0; padding: 0; }
  html, body {
    width: 1200px; height: 844px; overflow: hidden;
    background: var(--backdrop);
    font-family: "Open Sans", Arial, sans-serif;
  }
  .canvas {
    position: relative; width: 1200px; height: 844px;
    display: flex; align-items: center; justify-content: center; gap: 60px;
  }
  .card {
    position: relative; width: 520px; height: 297px; overflow: hidden;
    background: linear-gradient(120deg, var(--card-dark) 0%, var(--card-dark) 55%, var(--card-mid) 100%);
    box-shadow: 0 10px 28px rgba(0,0,0,0.45);
  }

  /* Contact side */
  .band { position: absolute; left: 0; right: 0; height: 13px; background: var(--accent-blue); }
  .band--top { top: 6px; }
  .band--bottom { bottom: 10px; }
  .contact {
    position: absolute; left: 250px; top: 112px; width: 260px;
    color: var(--text-light); text-align: center;
  }
  .contact__name {
    color: var(--accent-blue); font-weight: 700; font-size: 17px;
    letter-spacing: 0.3px; text-transform: uppercase; margin-bottom: 18px;
    white-space: nowrap;
  }
  .contact__line { font-size: 14px; line-height: 22px; }

  /* Brand side */
  .tab {
    position: absolute; width: 22px; height: 34px; background: var(--accent-blue);
  }
  .tab::after {
    content: ""; position: absolute; top: 0; bottom: 0; width: 3px; background: var(--tab-line);
  }
  .tab--right { right: 0; top: 38px; }
  .tab--right::after { left: 0; }
  .tab--left { left: 0; top: 196px; }
  .tab--left::after { right: 0; }
  .brand {
    position: absolute; left: 0; right: 0; top: 72px;
    display: flex; align-items: center; justify-content: center; gap: 12px;
  }
  .brand__dot {
    width: 22px; height: 22px; border-radius: 50%; background: var(--accent-blue);
  }
  .brand__name {
    color: var(--accent-blue); font-weight: 700; font-size: 24px; letter-spacing: 0.5px;
  }
  .services {
    position: absolute; left: 0; right: 0; top: 196px;
    color: var(--text-light); font-size: 13.5px; line-height: 20px; text-align: center;
  }
  .services__sep { margin: 0 6px; }
</style>
</head>
<body>
<main class="canvas">
  <section class="card card--contact" aria-label="Card contact side">
    <div class="band band--top"></div>
    <div class="contact">
      <h1 class="contact__name">Dennis Tollerby</h1>
      <p class="contact__line">SummitBladeair@Kestmail.com</p>
      <p class="contact__line">626-418-7352</p>
    </div>
    <div class="band band--bottom"></div>
  </section>

  <section class="card card--brand" aria-label="Card brand side">
    <div class="tab tab--right"></div>
    <div class="tab tab--left"></div>
    <div class="brand">
      <span class="brand__dot"></span>
      <span class="brand__name">Summit BladeAir, Inc.</span>
    </div>
    <div class="services">
      <p>Helicopter Flight Services<span class="services__sep">|</span>Aerial Filming &amp; Photography</p>
      <p>Flight School<span class="services__sep">|</span>Helicopter Tours</p>
    </div>
  </section>
</main>
</body>
</html>
```